Dorwin's Coating & Renewal Letterhead Design We want to revamp out old traditional letterhead with the new logo designs that are attached. We are working on getting all our company items from vehicles, business, cards, t-shirts, letterhead to match. This should include company colors, fonts, and flow of items that we have attached below.

Industry/Entity Type

Construction Company

Font styles to use
Sans Serif
Other font styles liked:
• Bold with outline

Colors
ec1f27
ffffff

Requirements
Must have
• Company Name: Dorwin's Coating & Renewal
• Address: 4728 SW 81st Ter Halverd cove fl 39417
• Office Number: (555) 413-2986
• Email: Dorwinrenewal@mailbrook.example
• License Number: KRT8046392
Nice to have
• Company Colors: red, white, black, and grey

```html
<!DOCTYPE html>
<html lang="en">
<head>
<meta charset="utf-8">
<title>Dorwin's Coating &amp; Renewal — Letterhead</title>
<link rel="stylesheet" href="https://fonts.googleapis.com/css2?family=Montserrat:wght@400;600;700;800&display=swap">
<style>
  :root {
    --brand-red: #ec1f27;
    --logo-red: #ee4b26;
    --ink: #2b2b2b;
    --body-ink: #333333;
    --swoosh-grey: #e8e8e8;
    --swoosh-pink: #fbd9d0;
    --stage: #cccccc;
    --paper: #ffffff;
  }
  * { box-sizing: border-box; margin: 0; padding: 0; }
  html, body {
    width: 904px; height: 1200px; overflow: hidden;
    background: var(--stage);
    font-family: "Montserrat", Arial, sans-serif;
  }
  .letterhead {
    position: absolute; left: 71px; top: 61px;
    width: 762px; height: 1076px;
    background: var(--paper); overflow: hidden;
  }
  .decor { position: absolute; inset: 0; width: 762px; height: 1076px; }
  .brand-name {
    position: absolute; left: 54px; top: 52px;
    color: var(--logo-red); font-weight: 800;
    font-size: 27px; line-height: 1.05; text-transform: uppercase; letter-spacing: 0.5px;
  }
  .contact {
    position: absolute; right: 58px; top: 45px;
    list-style: none; text-align: right;
    font-weight: 700; font-size: 14px; color: var(--ink);
  }
  .contact li { display: flex; justify-content: flex-end; align-items: center; gap: 7px; height: 18.5px; }
  .contact svg { width: 16px; height: 16px; flex: none; }
  .header-rule {
    position: absolute; left: 318px; right: 0; top: 122px;
    height: 2px; background: var(--brand-red);
  }
  .closing { position: absolute; left: 54px; top: 215px; font-size: 12px; color: var(--body-ink); }
  .signer-name { position: absolute; left: 54px; top: 246px; font-size: 20px; font-weight: 600; color: var(--ink); letter-spacing: 0.5px; }
  .signer-role { position: absolute; left: 55px; top: 271px; font-size: 14px; font-weight: 700; color: var(--ink); }
  .letter-body { position: absolute; left: 54px; top: 411px; width: 680px; font-size: 12px; line-height: 25px; color: var(--body-ink); }
  .letter-body p + p { margin-top: 25px; }
  .letter-body p.spaced { margin-top: 50px; }
  .footer-rule { position: absolute; left: 0; right: 0; top: 1025px; height: 2px; background: var(--brand-red); }
  .footer-address { position: absolute; left: 54px; top: 1043px; font-size: 15px; font-weight: 700; color: var(--ink); }
  .footer-license { position: absolute; right: 58px; top: 1043px; font-size: 15px; font-weight: 700; color: var(--brand-red); }
</style>
</head>
<body>
<main class="letterhead">
  <svg class="decor" viewBox="0 0 762 1076" aria-hidden="true">
    <defs>
      <linearGradient id="base-fade" x1="0" y1="0" x2="0" y2="1">
        <stop offset="0" stop-color="#f6f6f6" stop-opacity="0.9"/>
        <stop offset="1" stop-color="#f6f6f6" stop-opacity="0.3"/>
      </linearGradient>
    </defs>
    <path d="M0 237 C260 215 520 130 656 0 L700 0 C560 150 300 245 0 251 Z" fill="var(--swoosh-grey)"/>
    <path d="M452 190 C580 150 700 90 762 25 L762 70 C690 130 590 170 452 190 Z" fill="var(--swoosh-grey)"/>
    <path d="M0 842 C300 810 600 720 762 655 L762 920 C520 970 240 1010 0 1040 Z" fill="url(#base-fade)"/>
    <path d="M176 1076 C260 1030 380 990 446 990 C360 1010 280 1045 236 1076 Z" fill="var(--swoosh-pink)"/>
    <path d="M446 1076 C560 1030 690 995 762 986 L762 995 C660 1015 560 1045 510 1076 Z" fill="var(--swoosh-pink)"/>
  </svg>

  <h1 class="brand-name">Dorwin's<br>Coating &amp; Renewal</h1>

  <ul class="contact">
    <li>(555) 413-2986
      <svg viewBox="0 0 16 16"><circle cx="8" cy="8" r="7" fill="none" stroke="var(--brand-red)" stroke-width="1.2"/><path d="M5.5 4.5 l1.4-.4 .9 1.8-.9.7 c.4 1 1.1 1.7 2 2.1 l.7-.9 1.8.9-.4 1.4 c-3 .2-5.6-2.4-5.5-5.6z" fill="var(--brand-red)"/></svg>
    </li>
    <li>Dorwinrenewal@mailbrook.example
      <svg viewBox="0 0 16 16"><circle cx="8" cy="8" r="7" fill="none" stroke="var(--brand-red)" stroke-width="1.2"/><rect x="4.5" y="5.5" width="7" height="5" rx="0.6" fill="var(--brand-red)"/><path d="M4.8 5.8 8 8.4 11.2 5.8" fill="none" stroke="#fff" stroke-width="0.7"/></svg>
    </li>
    <li>www.dorwinrenewal.example
      <svg viewBox="0 0 16 16"><circle cx="8" cy="8" r="7" fill="none" stroke="var(--brand-red)" stroke-width="1.2"/><g fill="none" stroke="var(--brand-red)" stroke-width="0.7"><circle cx="8" cy="8" r="3.8"/><ellipse cx="8" cy="8" rx="1.6" ry="3.8"/><path d="M4.2 8h7.6M4.8 6h6.4M4.8 10h6.4"/></g></svg>
    </li>
  </ul>
  <div class="header-rule"></div>

  <p class="closing">Sincearly,</p>
  <p class="signer-name">MARA ELLIS</p>
  <p class="signer-role">Director</p>

  <section class="letter-body">
    <p>This is a sample letter that has been placed to demonstrate typing remat (Your Company).letterhead<br>
    design. When positioned properly, it will serve to work in harmony with all other elements letterhead.<br>
    This letterhead design is meant to project an image&nbsp; This letterhead design is meant project an image<br>
    of professionalism reliability. By using simple aligen we have created a very spacious feeling.<br>
    The simplicity suggest&nbsp; rengththe spaciousnes contributes haesthetics the layout. These basic<br>
    qualities along with the (Your Company)</p>
    <p>look and helps reinforce the (Your Company) brand. letterhead design is meant to project an image<br>
    design. When positioned properly, it will serve to work in harmony all the other elements letterhead.<br>
    sionalism and reliability.</p>
    <p class="spaced">This letterhead design is based on the (Form of your logo) form (Your Company) logo. Each stationery<br>
    we have created a very spacious feeling. The simplicity suggests strength the spaciousnes contribute<br>
    part of the (Form of your logo). This letterhead design is based on the (Form of your logo) form (Your<br>
    Company) logo. Each stationery we have created a very spacious feeling. The simplicity suggests<br>
    strength the spaciousnes contribute part of the (Form of your logo).</p>
  </section>

  <div class="footer-rule"></div>
  <p class="footer-address">4728 SW 81st Ter . Halverd Cove, Florida 39417</p>
  <p class="footer-license">KRT8046392</p>
</main>
</body>
</html>
```